Letter head / email signature/ contract document templates

We need a professional email signature and letterhead designed for our established carpentry and maintenance company. Our Logo (attached) was originally designed 6 years ago by design guru and we love it, looking for something to compliment it ( not a home job)

```html
<!DOCTYPE html>
<html lang="en">
<head>
<meta charset="utf-8">
<title>Harbourline Repair Co – Letterhead</title>
<link href="https://fonts.googleapis.com/css2?family=Open+Sans:wght@400;700&family=Roboto:wght@400&display=swap" rel="stylesheet">
<style>
  :root {
    --backdrop: #dcdcdc;
    --paper: #f7f7f7;
    --ink: #3f3f3f;
    --ink-dark: #333333;
    --brand-red: #d92027;
    --tool-grey: #8c8c8c;
    --signature-tone: #e4e4e4;
  }
  * { margin: 0; padding: 0; box-sizing: border-box; }
  html, body {
    width: 1153px;
    height: 1200px;
    overflow: hidden;
    background: var(--backdrop);
  }
  .letterhead {
    position: absolute;
    left: 167px;
    top: 30px;
    width: 818px;
    height: 1140px;
    background: var(--paper);
    box-shadow: 0 10px 30px rgba(0,0,0,0.12);
    overflow: hidden;
    font-family: "Open Sans", Arial, sans-serif;
    color: var(--ink);
  }
  .brand {
    position: absolute;
    left: 79px;
    top: 112px;
    display: flex;
    align-items: center;
    gap: 10px;
  }
  .brand-mark {
    width: 16px;
    height: 16px;
    background: var(--brand-red);
  }
  .brand-name {
    font-weight: 700;
    font-size: 25px;
    color: var(--ink-dark);
    letter-spacing: 0.2px;
  }
  .contact {
    position: absolute;
    left: 565px;
    top: 83px;
    font-family: "Roboto", Arial, sans-serif;
    font-size: 12.3px;
    line-height: 16px;
    color: var(--ink);
    list-style: none;
  }
  .contact li { display: flex; align-items: center; gap: 5px; }
  .contact .address { display: block; margin-bottom: 2px; }
  .contact svg { width: 11px; height: 11px; flex: none; }
  .contact li + li { margin-top: 1px; }
  .letter-body {
    position: absolute;
    left: 74px;
    top: 272px;
    width: 669px;
    font-size: 14.6px;
    line-height: 22px;
  }
  .letter-body p { text-align: justify; margin-bottom: 22px; }
  .letter-body .salutation,
  .letter-body .closing { text-align: left; }
  .signature {
    position: absolute;
    left: 74px;
    top: 847px;
    width: 97px;
    height: 90px;
    background: var(--signature-tone);
  }
  .footer-band {
    position: absolute;
    left: 0;
    bottom: 0;
    width: 818px;
    height: 50px;
  }
</style>
</head>
<body>
  <main class="letterhead">
    <header>
      <div class="brand">
        <span class="brand-mark"></span>
        <span class="brand-name">Harbourline Repair Co</span>
      </div>
      <ul class="contact">
        <li class="address">48 Maple Ridge Lane,<br>Brookfield, ON L5T 1K3</li>
        <li>
          <svg viewBox="0 0 12 12" aria-hidden="true"><path d="M1 5c0-2 2-3 5-3s5 1 5 3l-2 1-1-1.5H4L3 6z M3 6.5h6l1 4H2z" fill="var(--brand-red)"/></svg>
          905.555.0148
        </li>
        <li>
          <svg viewBox="0 0 12 12" aria-hidden="true"><rect x="1" y="2.5" width="10" height="7" fill="var(--brand-red)"/><path d="M1 2.5l5 4 5-4" stroke="#fff" stroke-width="1" fill="none"/></svg>
          hello@harbourlinerepair.com
        </li>
        <li>
          <svg viewBox="0 0 12 12" aria-hidden="true"><circle cx="6" cy="6" r="5" fill="var(--brand-red)"/><path d="M6 1v10M1 6h10" stroke="#fff" stroke-width="0.8"/></svg>
          www.harbourlinerepair.com
        </li>
      </ul>
    </header>

    <section class="letter-body">
      <p class="salutation">Dear customer,</p>
      <p>Lorem ipsum dolor sit amet, consectetur adipisicing elit, sed do eiusmod tempor incididunt ut labore et dolore magna aliqua. Ut enim ad minim veniam, quis nostrud exercitation ullamco laboris nisi ut aliquip ex ea commodo consequat. Duis aute irure dolor in reprehenderit in voluptate velit esse cillum dolore eu fugiat nulla pariatur. Excepteur sint occaecat cupidatat non proident, sunt in culpa qui officia deserunt mollit anim id est laborum.</p>
      <p>Lorem ipsum dolor sit amet, consectetur adipisicing elit, sed do eiusmod tempor incididunt ut labore et dolore magna aliqua. Ut enim ad minim veniam, quis nostrud exercitation ullamco laboris nisi ut aliquip ex ea commodo consequat. Duis aute irure dolor in reprehenderit in voluptate velit esse cillum dolore eu fugiat nulla pariatur. Excepteur sint occaecat cupidatat non proident, sunt in culpa qui officia deserunt mollit anim id est laborum.</p>
      <p>Lorem ipsum dolor sit amet, consectetur adipisicing elit, sed do eiusmod tempor incididunt ut labore et dolore magna aliqua. Ut enim ad minim veniam, quis nostrud exercitation ullamco laboris nisi ut aliquip ex ea commodo consequat. Duis aute irure dolor in reprehenderit in voluptate velit esse cillum dolore eu fugiat nulla pariatur. Excepteur sint occaecat cupidatat non proident, sunt in culpa qui officia deserunt mollit anim id est laborum.</p>
      <p>Lorem ipsum dolor sit amet, consectetur adipisicing elit, sed do eiusmod tempor incididunt ut labore et dolore magna aliqua. Ut enim ad minim veniam, quis nostrud exercitation ullamco laboris nisi ut aliquip ex ea commodo consequat. Duis aute irure dolor in reprehenderit.</p>
      <p class="closing">Yours Sincerely,</p>
    </section>

    <div class="signature" role="img" aria-label="Handwritten signature of the sender"></div>

    <svg class="footer-band" viewBox="0 0 818 50" aria-hidden="true">
      <rect x="0" y="28" width="170" height="22" fill="var(--ink-dark)"/>
      <rect x="175" y="28" width="580" height="22" fill="var(--brand-red)"/>
      <rect x="745" y="8" width="73" height="42" fill="var(--tool-grey)" opacity="0.55" role="img" aria-label="Paint roller illustration"/>
    </svg>
  </main>
</body>
</html>
```